New Company Business Card design

Looking for a corporate looking business card utilising my new logo design - the logo i would like embossed as one option and flat as another - simplistic but stylish - less is more - we are an import export business launching into the market - i would like a couple of options as main background - Grey or Black

```html
<!DOCTYPE html>
<html lang="en">
<head>
<meta charset="utf-8">
<title>Meridian Trade Partners – Business Card</title>
<link rel="stylesheet" href="https://fonts.googleapis.com/css2?family=Cinzel:wght@500&family=Arimo&display=swap">
<style>
  :root {
    --backdrop: #666666;
    --card-white: #ffffff;
    --card-charcoal: #2c2d2f;
    --charcoal-edge: #1e1f20;
    --brand-blue: #0a70c2;
    --brand-grey: #6d6e70;
    --ink: #1a1a1a;
    --divider: #c8c8c8;
    --card-edge: #8a8a8a;
  }
  * { margin: 0; padding: 0; box-sizing: border-box; }
  html, body { width: 1200px; height: 802px; overflow: hidden; }
  body { background: var(--backdrop); position: relative; font-family: "Arimo", Arial, sans-serif; }

  .card {
    position: absolute;
    top: 274px;
    width: 443px;
    height: 265px;
    border-bottom: 10px solid var(--card-edge);
  }
  .card--front { left: 136px; background: var(--card-white); }
  .card--back { left: 624px; background: var(--card-charcoal); border-bottom-color: var(--charcoal-edge); }

  .brand {
    position: absolute;
    left: 18px;
    top: 112px;
    width: 204px;
    display: flex;
    align-items: center;
    justify-content: center;
    gap: 8px;
  }
  .brand__dot { width: 14px; height: 14px; border-radius: 50%; background: var(--brand-blue); flex: none; }
  .brand__name {
    font-family: "Cinzel", Georgia, serif;
    font-weight: 500;
    font-size: 17px;
    letter-spacing: 0.5px;
    color: var(--brand-blue);
    line-height: 1.15;
    text-align: center;
  }

  .divider {
    position: absolute;
    left: 235px;
    top: 62px;
    width: 1px;
    height: 142px;
    background: var(--divider);
  }

  .person { position: absolute; left: 249px; top: 73px; }
  .person__name {
    font-family: "Cinzel", Georgia, serif;
    font-weight: 500;
    font-size: 19px;
    letter-spacing: 0.4px;
    line-height: 1.1;
  }
  .person__first { color: var(--brand-blue); }
  .person__last { color: var(--brand-grey); }
  .person__role { font-size: 13px; color: var(--ink); margin-top: 1px; }

  .contact {
    position: absolute;
    left: 248px;
    top: 126px;
    list-style: none;
    font-size: 13px;
    color: var(--ink);
  }
  .contact__item { display: flex; align-items: center; height: 15.8px; gap: 6px; }
  .contact__icon { width: 10px; height: 10px; fill: var(--brand-blue); flex: none; }

  .back-mark {
    position: absolute;
    left: 0;
    right: 0;
    top: 148px;
    padding-left: 50px;
    display: flex;
    align-items: center;
    justify-content: center;
    gap: 10px;
  }
  .back-mark__dot { width: 18px; height: 18px; border-radius: 50%; background: var(--brand-blue); }
  .back-mark__name {
    font-family: "Cinzel", Georgia, serif;
    font-weight: 500;
    font-size: 32px;
    line-height: 1;
    color: var(--card-white);
  }
</style>
</head>
<body>

<section class="card card--front" aria-label="Business card front">
  <div class="brand">
    <span class="brand__dot"></span>
    <span class="brand__name">Meridian Trade<br>Partners</span>
  </div>

  <div class="divider"></div>

  <div class="person">
    <p class="person__name"><span class="person__first">DANIEL</span> <span class="person__last">HAYES</span></p>
    <p class="person__role">Managing Director</p>
  </div>

  <ul class="contact">
    <li class="contact__item">
      <svg class="contact__icon" viewBox="0 0 10 10"><path d="M1 3.5C1 2 2.5 1.5 5 1.5S9 2 9 3.5L7.5 4.2 7 3H3L2.5 4.2Z"/><rect x="2" y="5" width="6" height="4" rx="0.8"/></svg>
      <span>044-555 210 834</span>
    </li>
    <li class="contact__item">
      <svg class="contact__icon" viewBox="0 0 10 10"><path d="M3 0.5h4a1 1 0 0 1 1 1v7a1 1 0 0 1-1 1H3a1 1 0 0 1-1-1v-7a1 1 0 0 1 1-1Zm0.4 1.2v5.6h3.2V1.7Z"/></svg>
      <span>044-555 210 834</span>
    </li>
    <li class="contact__item">
      <svg class="contact__icon" viewBox="0 0 10 10"><path d="M0.5 2h9v6h-9Zm0.8 0.8L5 5.6l3.7-2.8v-0.3H1.3Z"/></svg>
      <span>hello@meridiantrade.com</span>
    </li>
    <li class="contact__item">
      <svg class="contact__icon" viewBox="0 0 10 10"><circle cx="5" cy="5" r="4.5"/><path d="M3 3.5 5 3l1.5 1.5L5 6.5 3.5 6Z" fill="#fff"/></svg>
      <span>www.meridiantrade.com</span>
    </li>
  </ul>
</section>

<section class="card card--back" aria-label="Business card back">
  <div class="back-mark">
    <span class="back-mark__dot"></span>
    <span class="back-mark__name">Meridian</span>
  </div>
</section>

</body>
</html>
```